Oil and Gas Exploration and Production company needs a business card design

We need a business card design using our logo and colors in the logo. We want a mainstream design.

```html
<!DOCTYPE html>
<html lang="en">
<head>
<meta charset="utf-8">
<title>Tarra Oil &amp; Gas — Business Card</title>
<link href="https://fonts.googleapis.com/css2?family=Open+Sans:wght@400;600;700;800&display=swap" rel="stylesheet">
<style>
  :root {
    --ink: #141414;
    --gold: #c9962b;
    --paper: #ffffff;
    --muted: #555555;
    --stage: #2b2b2b;
  }
  * { box-sizing: border-box; margin: 0; padding: 0; }
  html, body {
    width: 1200px; height: 900px; overflow: hidden;
    background: var(--stage);
    font-family: "Open Sans", Arial, sans-serif;
  }
  .stage {
    position: relative; width: 1200px; height: 900px;
  }
  .card {
    position: absolute; left: 300px;
    width: 600px; height: 343px;
    background: var(--paper);
    box-shadow: 0 10px 30px rgba(0,0,0,.45);
    overflow: hidden;
  }
  .card--front { top: 80px; }
  .card--back { top: 477px; }

  /* wordmark */
  .wordmark {
    display: flex; align-items: center; gap: 12px;
    font-weight: 800; color: var(--ink);
    letter-spacing: -0.5px; line-height: 1;
  }
  .wordmark__dot {
    width: 30px; height: 30px; border-radius: 50%;
    background: var(--gold); flex: none;
  }

  /* front */
  .card--front .wordmark {
    position: absolute; left: 0; right: 0; top: 125px;
    justify-content: center; font-size: 44px;
  }
  .website {
    position: absolute; left: 0; right: 0; top: 215px;
    text-align: center; font-size: 13px; letter-spacing: 5px;
    color: var(--muted);
  }

  /* back */
  .band {
    position: absolute; left: 0; top: 0; bottom: 0; width: 64px;
    background: var(--gold);
  }
  .contact-icons {
    position: absolute; left: 22px; top: 190px;
    display: flex; flex-direction: column; gap: 14px;
  }
  .contact-icons svg { width: 20px; height: 20px; display: block; }
  .contact-icons .gap { height: 14px; }

  .card--back .wordmark {
    position: absolute; left: 50px; top: 92px; font-size: 40px;
  }
  .identity {
    position: absolute; right: 36px; top: 40px; text-align: right;
  }
  .identity__name { font-weight: 800; font-size: 17px; color: var(--ink); letter-spacing: .5px; }
  .identity__title { font-weight: 600; font-size: 13px; color: var(--gold); letter-spacing: .5px; }
  .tab {
    position: absolute; right: 0; top: 36px; width: 14px; height: 48px;
    background: var(--ink);
  }
  .details {
    position: absolute; left: 118px; top: 178px;
    font-size: 15px; color: var(--muted); line-height: 21px;
  }
  .details__address { margin-bottom: 20px; }
</style>
</head>
<body>
<main class="stage">

  <section class="card card--front" aria-label="Card front">
    <div class="wordmark"><span class="wordmark__dot"></span>Tarra Oil &amp; Gas</div>
    <p class="website">www.tarraoil&amp;gas.com</p>
  </section>

  <section class="card card--back" aria-label="Card back">
    <div class="band"></div>
    <div class="contact-icons" aria-hidden="true">
      <svg viewBox="0 0 20 20"><path d="M10 2a5.5 5.5 0 0 0-5.5 5.5C4.5 12 10 18 10 18s5.5-6 5.5-10.5A5.5 5.5 0 0 0 10 2zm0 7.5a2 2 0 1 1 0-4 2 2 0 0 1 0 4z" fill="var(--ink)"/></svg>
      <div class="gap"></div>
      <svg viewBox="0 0 20 20"><path d="M4 3h3l1.5 4-2 1.2a9 9 0 0 0 5.3 5.3L13 11.5l4 1.5v3a1.5 1.5 0 0 1-1.6 1.5C8.6 17 3 11.4 2.5 4.6A1.5 1.5 0 0 1 4 3z" fill="var(--ink)"/></svg>
      <svg viewBox="0 0 20 20"><rect x="6" y="2" width="8" height="16" rx="1.5" fill="var(--ink)"/><rect x="7.5" y="4" width="5" height="10" fill="var(--gold)"/></svg>
      <svg viewBox="0 0 20 20"><rect x="3" y="8" width="14" height="8" rx="1" fill="var(--ink)"/><rect x="6" y="3" width="8" height="6" fill="var(--ink)"/><rect x="6" y="12" width="8" height="1.5" fill="var(--gold)"/></svg>
      <svg viewBox="0 0 20 20"><rect x="2" y="5" width="16" height="11" rx="1" fill="var(--ink)"/><path d="M2.5 5.5 10 11l7.5-5.5" stroke="var(--gold)" stroke-width="1.4" fill="none"/></svg>
    </div>

    <div class="wordmark"><span class="wordmark__dot"></span>Tarra Oil &amp; Gas</div>

    <div class="identity">
      <p class="identity__name">MARK ELLORY</p>
      <p class="identity__title">PRESIDENT</p>
    </div>
    <div class="tab"></div>

    <address class="details" style="font-style:normal">
      <p class="details__address">4127 Harlow Avenue<br>Brookfield, NY 11210</p>
      <p>512 7740 3196</p>
      <p>847 2261 9054</p>
      <p>833 5904 1172</p>
      <p>info@tarraoil&amp;gas.com</p>
    </address>
  </section>

</main>
</body>
</html>
```